Business Card Design Can you design a business card design? Looking for something unique and differe

Can you design a business card design? Looking for something unique and different. Can you design a business card design? Looking for something unique and different.Can you design a business card design? Looking for something unique and different.Can you design a business card design? Looking for something unique and different.Can you design a business card design? Looking for something unique and different.Can you design a business card design? Looking for something unique and different.

Industry/Entity Type

Business

Contact Information for Business Card

Can you design a business card design? Looking for something unique and different.

Font styles to use
Serif

```html
<!DOCTYPE html>
<html lang="en">
<head>
<meta charset="utf-8">
<title>Medora Business Card</title>
<link href="https://fonts.googleapis.com/css2?family=Quicksand:wght@600;700&family=Open+Sans:ital,wght@0,400;0,600;1,400&display=swap" rel="stylesheet">
<style>
  :root {
    --backdrop: #dcdcdc;
    --card: #ffffff;
    --violet: #8a6aa3;
    --ink: #141414;
    --grey: #8c8c8c;
    --light-grey: #c8c8c8;
    --contact-text: #f2f2f2;
  }
  html, body {
    margin: 0;
    width: 1200px;
    height: 852px;
    overflow: hidden;
    background: var(--backdrop);
  }
  .stage {
    position: relative;
    width: 1200px;
    height: 852px;
  }
  .card {
    position: absolute;
    top: 276px;
    width: 520px;
    height: 300px;
    background: var(--card);
    border-radius: 12px;
    overflow: hidden;
    box-shadow: 0 6px 18px rgba(0,0,0,0.18);
  }
  .card--front { left: 50px; }
  .card--back { left: 630px; }

  .brand {
    position: absolute;
    display: flex;
    align-items: center;
    gap: 14px;
    white-space: nowrap;
  }
  .brand__mark {
    width: 20px;
    height: 20px;
    background: var(--violet);
    flex: none;
  }
  .brand__name {
    font-family: "Quicksand", sans-serif;
    font-weight: 700;
    font-size: 38px;
    color: var(--violet);
    letter-spacing: 0.3px;
    line-height: 1;
    white-space: nowrap;
  }
  .card--front .brand {
    left: 50%;
    top: 50%;
    transform: translate(-50%, -50%);
  }
  .card--back .brand {
    left: 36px;
    top: 136px;
  }
  .card--back .brand__name { font-size: 28px; }

  .wave {
    position: absolute;
    inset: 0;
    width: 520px;
    height: 300px;
  }

  .holder {
    position: absolute;
    right: 24px;
    top: 18px;
    text-align: right;
  }
  .holder__name {
    font-family: "Quicksand", sans-serif;
    font-weight: 700;
    font-size: 17px;
    color: var(--violet);
    margin: 0;
    white-space: nowrap;
  }
  .holder__role {
    font-family: "Open Sans", sans-serif;
    font-style: italic;
    font-size: 10px;
    color: var(--ink);
    margin: 2px 0 0;
    white-space: nowrap;
  }

  .contacts {
    position: absolute;
    right: 18px;
    top: 108px;
    margin: 0;
    padding: 0;
    list-style: none;
    font-family: "Open Sans", sans-serif;
    font-size: 10.5px;
    color: var(--contact-text);
    text-align: right;
  }
  .contacts li {
    display: flex;
    align-items: center;
    justify-content: flex-end;
    gap: 8px;
    height: 18px;
    white-space: nowrap;
  }
  .icon {
    width: 11px;
    height: 11px;
    flex: none;
  }
</style>
</head>
<body>
<main class="stage">

  <section class="card card--front" aria-label="Card front">
    <div class="brand">
      <span class="brand__mark"></span>
      <span class="brand__name">Medora cost care</span>
    </div>
  </section>

  <section class="card card--back" aria-label="Card back">
    <svg class="wave" viewBox="0 0 520 300" aria-hidden="true">
      <path d="M0,262 C90,250 170,280 220,300 L0,300 Z" fill="var(--light-grey)"/>
      <path d="M0,278 C90,272 150,290 190,300 L0,300 Z" fill="var(--grey)"/>
      <path d="M520,56 C420,62 364,86 320,134 C276,182 214,266 80,296" fill="none" stroke="var(--violet)" stroke-width="5"/>
      <path d="M520,72 C430,78 380,100 335,145 C290,190 230,270 100,300 L520,300 Z" fill="var(--ink)"/>
    </svg>

    <div class="holder">
      <p class="holder__name">Your Long Name</p>
      <p class="holder__role">Managing Director</p>
    </div>

    <div class="brand">
      <span class="brand__name">Medora cost care</span>
    </div>

    <ul class="contacts">
      <li>00.00.00.0000
        <svg class="icon" viewBox="0 0 12 12"><path d="M2 1h3l1 3-2 1a7 7 0 0 0 3 3l1-2 3 1v3c-6 0-10-4-10-9z" fill="var(--violet)"/></svg>
      </li>
      <li>00.00.00.0000
        <svg class="icon" viewBox="0 0 12 12"><rect x="1" y="4" width="10" height="7" rx="1" fill="var(--violet)"/><rect x="3" y="1" width="6" height="4" fill="var(--violet)"/></svg>
      </li>
      <li>www.yourwebsite.com
        <svg class="icon" viewBox="0 0 12 12"><circle cx="6" cy="6" r="5" fill="none" stroke="var(--violet)" stroke-width="1.5"/><path d="M1 6h10M6 1v10" stroke="var(--violet)" stroke-width="1"/></svg>
      </li>
      <li>yourname@yourwebsite.com
        <svg class="icon" viewBox="0 0 12 12"><rect x="0.5" y="2" width="11" height="8" fill="var(--violet)"/><path d="M1 2.5l5 4 5-4" fill="none" stroke="var(--ink)" stroke-width="1"/></svg>
      </li>
      <li>Your Commercial or office address
        <svg class="icon" viewBox="0 0 12 12"><path d="M6 11C3 7 2 5.5 2 4.5a4 4 0 0 1 8 0C10 5.5 9 7 6 11z" fill="var(--violet)"/><circle cx="6" cy="4.5" r="1.4" fill="var(--ink)"/></svg>
      </li>
    </ul>
  </section>

</main>
</body>
</html>
```